IT consulting company looking for a modern business design for a website and a new logo

We are the IT-consulting company VelmaTrix from Germany and need a new and modern business website and a new logo. We are specialized in output management. Our services include business analysis, outsourcing, development, training and project leading. We wish for a design with nature pictures (mountains, lakes, rivers, forests, etc.) for our company with the colors green and blue. If it is possible, a slow-mo video of a nature scene. The design should be responsive and the menu should change to a hamburger menu. The following are: • Services / Solutions 1. Output Management 2. Outsourcing 3. Development 4. Business Analyst 5. Training • Partners • Careers • About Us 1. Project A 2. Project B 3. Project C • Contact Notes for the following categories: For "Services / Solutions" we want to conclude some contents from all the sub-points and sub-points below. Additionally, we would like to see some sub-point under "Services / Solutions". For Output Management: "5 Benefits of Output Management Systems (OMS) - OMS Simplifies and Accelerates External Communication - Helps Reduce Communication Mistakes - Provides Customers With Fast and Secure Responses to your questions - Employees can focus on the essential as they can access prepared templates - Companies get complete transparency about their communication "The point" partner does not have sub-points. The content here is a quote and the logo from the company Brel. For now, just placeholders on this site. The next point wants to be "career" without sub-point and wants to contain some text. Carrer options wants to be listed here. Next point wants to be "About us", where we need sub-points which we do not know exactly at this moment, but they will contain text. By clicking directly on "About us" we want to include pictures and texts about 6 employees for which we only need placeholders at the moment. The last point wants to be "contact", where customers can send us messages. The main page should include a story about our company, which can be a placeholder for now. For reference, designs have a look at: https://brelvanto.de/ https://www.tarnopix.com/ https://www.pldrive.de/ We prefer WordPress designs, created with the plugin ELEMENTOR, so that we can easily edit the content by ourselves. The final design should look professional, competent and modern.

Target Market(s)

With our website, we want to reach the following target groups. <br> <br> <br> <br> <br> <br> <br> <br> <br> <br> <br> <br> <br> <br> <br> <br> <br> <br> <br> <br> <br> <br> <br> <br> <br> <br> <br> <br> <br> <br> <br> <br> <br> <br> <br> <br> <br> <br> <br> <br> <br> <br> <br> <br> <br> <br> <br> <br> <br>

Industry/Entity Type

Consulting

Logo Text

(optionally) VelmaTrix

Font styles to use
Sans Serif

Colors

Designer to choose colors to be used in the design.

Requirements
Must have
• 1. Outsourcing 3. Development 4. Business Analyst 5. Training • Partners • Careers • About Us 1. Project A 2. Project B 3. Project C • Contact The above-mentioned background picture with nature motifs (mountains, lakes, rivers, forests, etc.). WordPress design in primary colors blue and green.
Nice to have
• ELEMENTOR template. Effects for the background pictures. Counter of all successful projects for Output Management, Business Analyst and Training

```html
<!DOCTYPE html>
<html lang="de">
<head>
<meta charset="utf-8">
<title>VelmaTrix – IT Consulting</title>
<link rel="stylesheet" href="https://fonts.googleapis.com/css2?family=Poppins:wght@500;600;700&family=Open+Sans:wght@400;600;700&display=swap">
<style>
:root{
  --blue:#1565b8;
  --blue-dark:#0f4f96;
  --logo-blue:#1d5f9e;
  --green:#6aaf16;
  --green-dark:#5a9a10;
  --ink:#222;
  --text:#444;
  --muted:#666;
  --bg-light:#f1f1f1;
  --panel-dark:#2f2f2f;
  --white:#fff;
}
*{box-sizing:border-box;margin:0;padding:0}
html,body{width:1200px;height:4141px;overflow:hidden}
body{position:relative;font-family:"Open Sans",sans-serif;color:var(--text);background:var(--white)}
.abs{position:absolute}
.btn{position:absolute;display:flex;align-items:center;justify-content:center;background:var(--green);color:var(--white);font-family:"Open Sans",sans-serif;font-weight:700;text-transform:uppercase;border-radius:2px;box-shadow:0 2px 4px rgba(0,0,0,.15)}

/* header + hero */
.hero{left:0;top:0;width:1200px;height:708px;background:linear-gradient(180deg,#ffffff 0%,#ffffff 9%,#c9d8ea 14%,#6f95c4 30%,#2d5f9e 55%,#1d467e 80%,#163a6a 100%)}
.logo{left:145px;top:30px;font-family:"Poppins",sans-serif;font-weight:700;font-size:35px;color:var(--logo-blue);letter-spacing:.3px}
.nav{left:559px;top:44px;display:flex;gap:27px;font-family:"Poppins",sans-serif;font-weight:500;font-size:13px;color:#222}
.hero-title{left:604px;top:330px;font-family:"Poppins",sans-serif;font-weight:700;font-size:50px;color:var(--white);text-shadow:0 2px 6px rgba(0,0,0,.25)}
.hero-sub{left:604px;top:396px;font-family:"Poppins",sans-serif;font-weight:600;font-size:23px;color:var(--white)}
.hero-btn{left:607px;top:456px;width:142px;height:50px;font-size:16px}

/* services */
.services{left:0;top:708px;width:1200px;height:913px;background:linear-gradient(135deg,#f7f7f7,#ececec 50%,#f5f5f5)}
.section-title{position:absolute;left:0;width:1200px;text-align:center;font-family:"Poppins",sans-serif;font-weight:700;font-size:32px;color:var(--ink)}
.svc-card{position:absolute;width:288px;height:345px;background:var(--white);box-shadow:0 2px 10px rgba(0,0,0,.06);text-align:center}
.svc-card svg{position:absolute;left:104px;top:30px}
.svc-card .rule{position:absolute;left:124px;top:134px;width:40px;height:2px;background:#3b86d6}
.svc-card h3{position:absolute;top:150px;width:100%;font-family:"Poppins",sans-serif;font-weight:600;font-size:18px;color:var(--ink)}
.svc-card p{position:absolute;top:190px;left:40px;width:208px;font-size:14px;line-height:21px;color:#333}
.svc-card .btn{left:92px;top:275px;width:104px;height:31px;font-size:11.5px}
.svc-all{background:linear-gradient(160deg,#2d78c8,#1a5aa6 60%,#174b8a)}
.svc-all .btn{left:45px;top:152px;width:203px;height:42px;font-size:16px}

/* welcome */
.welcome-photo{left:145px;top:1670px;width:510px;height:550px;background:linear-gradient(135deg,#3a3a3a,#5a5550 50%,#8a6a50)}
.welcome-box{left:577px;top:1727px;width:515px;height:454px;background:var(--white)}
.welcome-box .pre{position:absolute;left:43px;top:34px;font-family:"Poppins",sans-serif;font-weight:500;font-size:23px;color:#222}
.welcome-box h2{position:absolute;left:37px;top:62px;font-family:"Poppins",sans-serif;font-weight:700;font-size:42px;color:var(--ink)}
.welcome-box .rule{position:absolute;left:45px;top:124px;width:70px;height:3px;background:linear-gradient(90deg,var(--blue) 0 45%,transparent 45% 60%,var(--blue) 60%)}
.welcome-box .lead{position:absolute;left:45px;top:156px;width:440px;font-size:17px;line-height:25px;color:#222}
.welcome-box .body{position:absolute;left:45px;top:231px;width:455px;font-size:15px;line-height:23px;color:#444}
.welcome-box .btn{left:45px;top:382px;width:126px;height:38px;font-size:14.5px}

/* careers */
.careers{left:0;top:2281px;width:1200px;height:690px;background:var(--blue)}
.careers .section-title{color:var(--white);top:48px}
.job{position:absolute;width:296px;height:246px;background:var(--white)}
.job svg{position:absolute;left:30px;top:26px}
.job h3{position:absolute;left:30px;top:103px;font-family:"Open Sans",sans-serif;font-weight:600;font-size:16px;color:#222}
.job .date{position:absolute;left:30px;top:127px;font-size:12.5px;color:#555}
.job .meta{position:absolute;left:30px;top:158px;font-size:12.5px;color:#555;display:flex;align-items:center;gap:6px}
.job .btn{left:30px;top:199px;width:95px;height:24px;font-size:12px}

/* partners */
.partner-row{left:0;top:3150px;width:1200px;height:60px}
.partner{position:absolute;top:12px;height:28px;border-radius:3px}

/* contact map */
.map{left:0;top:3289px;width:1200px;height:450px;background:linear-gradient(135deg,#ececec,#e2e4e6 60%,#dfe6e0)}
.contact-panel{left:771px;top:3289px;width:429px;height:450px;background:var(--panel-dark);border-top-left-radius:90px}
.contact-panel h2{position:absolute;left:79px;top:62px;font-family:"Poppins",sans-serif;font-weight:700;font-size:32px;color:var(--white)}
.c-item{position:absolute;left:77px;display:flex;gap:18px;color:var(--white)}
.c-item .dot{width:31px;height:31px;border-radius:50%;background:#2a86e0;display:flex;align-items:center;justify-content:center;flex:none;margin-top:4px}
.c-item .lbl{font-size:16px;line-height:21px}
.c-item .val{font-size:21px;line-height:26px}

/* footer */
.footer{left:0;top:3739px;width:1200px;height:402px;background:var(--blue)}
.footer .flogo{position:absolute;left:167px;top:122px;font-family:"Poppins",sans-serif;font-weight:700;font-size:42px;color:var(--white)}
.fhead{position:absolute;top:48px;font-family:"Open Sans",sans-serif;font-weight:700;font-size:12px;color:var(--white);text-transform:uppercase}
.field{position:absolute;left:474px;width:229px;background:var(--white);font-size:11px;color:#444;padding:8px 10px}
.submit{position:absolute;left:474px;top:215px;width:229px;height:39px;background:var(--green);color:var(--white);font-family:"Poppins",sans-serif;font-weight:700;font-size:18px;display:flex;align-items:center;justify-content:center}
.fmenu{position:absolute;left:774px;top:78px;list-style:none;font-size:11px;line-height:17.6px;color:var(--white)}
.social{position:absolute;left:960px;display:flex;align-items:center;gap:12px;font-size:11.5px;color:var(--white)}
.social span.c{width:25px;height:25px;border-radius:50%;background:#0c2f5a}
.footer .line{position:absolute;left:140px;top:319px;width:915px;height:1px;background:rgba(255,255,255,.35)}
.copy{position:absolute;top:361px;width:1200px;text-align:center;font-size:11px;color:var(--white)}
</style>
</head>
<body>

<!-- Header and hero -->
<section class="abs hero" role="img" aria-label="Mountain landscape photo with a hiker standing on a rocky summit under snowy peaks, blue tones"></section>
<div class="abs logo">VelmaTrix</div>
<nav class="abs nav"><span>HOME</span><span>SERVICES</span><span>PARTNER</span><span>KARRIERE</span><span>ÜBER UNS</span><span>KONTAKT</span></nav>
<h1 class="abs hero-title">Business Analysis</h1>
<p class="abs hero-sub">Lorem Ipsum is simply dummy text</p>
<a class="btn hero-btn">Read More</a>

<!-- Services -->
<section class="abs services">
  <h2 class="section-title" style="top:52px">OUR SERVICES</h2>

  <div class="svc-card" style="left:151px;top:138px">
    <svg width="80" height="90" viewBox="0 0 80 90" fill="#333"><circle cx="40" cy="12" r="7"/><rect x="32" y="21" width="16" height="14" rx="3"/><path d="M40 36v12M40 48L18 60M40 48l22 12" stroke="#333" stroke-width="3" fill="none"/><circle cx="14" cy="66" r="6"/><rect x="6" y="74" width="16" height="12" rx="3"/><circle cx="66" cy="66" r="6"/><rect x="58" y="74" width="16" height="12" rx="3"/><rect x="36" y="52" width="8" height="8" fill="#2a7ad0"/></svg>
    <span class="rule"></span><h3>Output Management</h3>
    <p>Lorem ipsum dolor sit amet consectetur adipiscing elit sed do eiusmod tempor.</p>
    <a class="btn">Read More</a>
  </div>
  <div class="svc-card" style="left:456px;top:138px">
    <svg width="80" height="90" viewBox="0 0 80 90"><rect x="20" y="8" width="40" height="34" rx="3" fill="none" stroke="#333" stroke-width="4"/><circle cx="40" cy="25" r="9" fill="none" stroke="#333" stroke-width="3"/><path d="M35 25l4 4 7-8" stroke="#333" stroke-width="3" fill="none"/><rect x="2" y="46" width="16" height="22" fill="#333"/><rect x="62" y="46" width="16" height="22" fill="#333"/><path d="M18 52h14l10 8-8 4M62 52H48l-8 10" stroke="#333" stroke-width="4" fill="none"/><path d="M28 72c8 6 16 6 24 0" stroke="#2a7ad0" stroke-width="3" fill="none"/></svg>
    <span class="rule"></span><h3>Outsourcing</h3>
    <p>Lorem ipsum dolor sit amet consectetur adipiscing elit sed do eiusmod tempor.</p>
    <a class="btn">Read More</a>
  </div>
  <div class="svc-card" style="left:763px;top:138px">
    <svg width="80" height="90" viewBox="0 0 80 90"><circle cx="36" cy="36" r="22" fill="none" stroke="#333" stroke-width="10" stroke-dasharray="8 5"/><circle cx="36" cy="36" r="10" fill="#333"/><path d="M42 42l26 26" stroke="#333" stroke-width="9" stroke-linecap="round"/><circle cx="66" cy="66" r="3" fill="#2a7ad0"/></svg>
    <span class="rule"></span><h3>Entwicklung</h3>
    <p>Lorem ipsum dolor sit amet consectetur adipiscing elit sed do eiusmod tempor.</p>
    <a class="btn">Read More</a>
  </div>
  <div class="svc-card" style="left:151px;top:500px">
    <svg width="80" height="90" viewBox="0 0 80 90"><rect x="24" y="6" width="50" height="40" fill="none" stroke="#333" stroke-width="4"/><rect x="34" y="28" width="5" height="12" fill="#333"/><rect x="44" y="22" width="5" height="18" fill="#333"/><rect x="54" y="16" width="5" height="24" fill="#333"/><circle cx="14" cy="14" r="7" fill="#333"/><rect x="6" y="23" width="16" height="24" rx="3" fill="#333"/><path d="M22 28l14-8" stroke="#333" stroke-width="3"/><path d="M49 46L36 70M49 46l13 24M49 46v24" stroke="#333" stroke-width="4"/><rect x="8" y="47" width="5" height="22" fill="#333"/><rect x="15" y="47" width="5" height="22" fill="#333"/></svg>
    <span class="rule"></span><h3>Business Analyst</h3>
    <p>Lorem ipsum dolor sit amet consectetur adipiscing elit sed do eiusmod tempor.</p>
    <a class="btn">Read More</a>
  </div>
  <div class="svc-card" style="left:456px;top:500px">
    <svg width="80" height="90" viewBox="0 0 80 90"><rect x="17" y="4" width="46" height="38" fill="none" stroke="#333" stroke-width="4"/><circle cx="40" cy="17" r="6" fill="#333"/><rect x="31" y="25" width="18" height="12" rx="3" fill="#333"/><circle cx="22" cy="54" r="5" fill="#333"/><circle cx="40" cy="54" r="5" fill="#333"/><circle cx="58" cy="54" r="5" fill="#333"/><rect x="14" y="62" width="16" height="14" rx="3" fill="#2a7ad0"/><rect x="32" y="62" width="16" height="14" rx="3" fill="#2a7ad0"/><rect x="50" y="62" width="16" height="14" rx="3" fill="#2a7ad0"/></svg>
    <span class="rule"></span><h3>Schulungen</h3>
    <p>Lorem ipsum dolor sit amet consectetur adipiscing elit sed do eiusmod tempor.</p>
    <a class="btn">Read More</a>
  </div>
  <div class="svc-card svc-all" style="left:763px;top:500px" role="img" aria-label="Blue-tinted mountain photo behind the link to all services">
    <a class="btn">View All Services</a>
  </div>
</section>

<!-- Welcome -->
<div class="abs welcome-photo" role="img" aria-label="Photo of hands holding a tablet showing business charts, with a coffee cup on a dark table"></div>
<section class="abs welcome-box">
  <p class="pre">Welcome to</p>
  <h2>VelmaTrix</h2>
  <span class="rule"></span>
  <p class="lead">Led ut perspiciatis unde omnis iste natus error sit voluptatem accusantium doloremque.</p>
  <p class="body">At vero eos et accusamus et iusto odio dignissimos ducimus qui blanditiis praesentium voluptatum deleniti atque corrupti quos dolores et quas molestias excepturi sint occaecati cupiditate non provident, similique sunt in culpa qui officia deserunt mollitia animi, id est laborum et dolorum fuga</p>
  <a class="btn">Read More</a>
</section>

<!-- Careers -->
<section class="abs careers">
  <h2 class="section-title">KARRIERE</h2>

  <div class="job" style="left:145px;top:130px">
    <svg width="60" height="60" viewBox="0 0 60 60" fill="none" stroke="#1565b8" stroke-width="2"><rect x="12" y="6" width="40" height="28"/><path d="M18 28V20M26 28V14M34 28V18M42 28V10"/><circle cx="8" cy="12" r="4"/><path d="M4 36V20h8v16M32 34L22 56M32 34l10 22M32 34v22"/></svg>
    <h3>Business Analyst</h3><p class="date">Posted on September 10, 2018</p>
    <p class="meta"><svg width="10" height="12" viewBox="0 0 10 12"><path d="M5 0a4 4 0 014 4c0 3-4 8-4 8S1 7 1 4a4 4 0 014-4z" fill="#666"/><circle cx="5" cy="4" r="1.5" fill="#fff"/></svg>Marlow Creek, PA &nbsp;|&nbsp; <svg width="11" height="11" viewBox="0 0 11 11" fill="none" stroke="#666"><circle cx="5.5" cy="5.5" r="4.5"/><path d="M5.5 3v3h2"/></svg>Full/Part-time</p>
    <a class="btn">Apply Now</a>
  </div>
  <div class="job" style="left:453px;top:130px">
    <svg width="60" height="60" viewBox="0 0 60 60" fill="none" stroke="#1565b8" stroke-width="2"><circle cx="28" cy="20" r="12"/><path d="M8 56c0-14 8-20 20-20s20 6 20 20"/><circle cx="46" cy="10" r="6"/><path d="M24 38l4 8 4-8"/></svg>
    <h3>Project Manager</h3><p class="date">Posted on September 10, 2018</p>
    <p class="meta"><svg width="10" height="12" viewBox="0 0 10 12"><path d="M5 0a4 4 0 014 4c0 3-4 8-4 8S1 7 1 4a4 4 0 014-4z" fill="#666"/><circle cx="5" cy="4" r="1.5" fill="#fff"/></svg>Marlow Creek, PA &nbsp;|&nbsp; <svg width="11" height="11" viewBox="0 0 11 11" fill="none" stroke="#666"><circle cx="5.5" cy="5.5" r="4.5"/><path d="M5.5 3v3h2"/></svg>Full/Part-time</p>
    <a class="btn">Apply Now</a>
  </div>
  <div class="job" style="left:760px;top:130px">
    <svg width="60" height="60" viewBox="0 0 60 60" fill="none" stroke="#1565b8" stroke-width="2"><rect x="6" y="4" width="44" height="32" rx="2"/><path d="M22 14l-6 6 6 6M34 14l6 6-6 6M30 12l-4 16"/><rect x="6" y="40" width="30" height="12"/><circle cx="46" cy="48" r="5"/></svg>
    <h3>Software Engineer</h3><p class="date">Posted on September 10, 2018</p>
    <p class="meta"><svg width="10" height="12" viewBox="0 0 10 12"><path d="M5 0a4 4 0 014 4c0 3-4 8-4 8S1 7 1 4a4 4 0 014-4z" fill="#666"/><circle cx="5" cy="4" r="1.5" fill="#fff"/></svg>Marlow Creek, PA &nbsp;|&nbsp; <svg width="11" height="11" viewBox="0 0 11 11" fill="none" stroke="#666"><circle cx="5.5" cy="5.5" r="4.5"/><path d="M5.5 3v3h2"/></svg>Full/Part-time</p>
    <a class="btn">Apply Now</a>
  </div>
  <div class="job" style="left:145px;top:388px">
    <svg width="74" height="60" viewBox="0 0 74 60" fill="none" stroke="#1565b8" stroke-width="2"><rect x="26" y="22" width="22" height="18"/><path d="M30 22v-8a7 7 0 0114 0v8"/><circle cx="37" cy="31" r="2"/><path d="M4 10h16M4 30h18M4 50h16M54 10h16M52 30h18M54 50h16"/><circle cx="4" cy="10" r="3"/><circle cx="4" cy="50" r="3"/><circle cx="70" cy="10" r="3"/><circle cx="70" cy="50" r="3"/></svg>
    <h3>IT Security</h3><p class="date">Posted on September 10, 2018</p>
    <p class="meta"><svg width="10" height="12" viewBox="0 0 10 12"><path d="M5 0a4 4 0 014 4c0 3-4 8-4 8S1 7 1 4a4 4 0 014-4z" fill="#666"/><circle cx="5" cy="4" r="1.5" fill="#fff"/></svg>Marlow Creek, PA &nbsp;|&nbsp; <svg width="11" height="11" viewBox="0 0 11 11" fill="none" stroke="#666"><circle cx="5.5" cy="5.5" r="4.5"/><path d="M5.5 3v3h2"/></svg>Full/Part-time</p>
    <a class="btn">Apply Now</a>
  </div>
  <div class="job" style="left:453px;top:388px">
    <svg width="60" height="60" viewBox="0 0 60 60" fill="none" stroke="#1565b8" stroke-width="2"><circle cx="30" cy="30" r="9"/><path d="M21 30h18M30 21v18"/><rect x="2" y="4" width="16" height="12"/><rect x="42" y="4" width="16" height="12"/><rect x="2" y="44" width="16" height="12"/><rect x="42" y="44" width="16" height="12"/><path d="M18 14l6 8M42 14l-6 8M18 46l6-8M42 46l-6-8"/></svg>
    <h3>Data Scientist</h3><p class="date">Posted on September 10, 2018</p>
    <p class="meta"><svg width="10" height="12" viewBox="0 0 10 12"><path d="M5 0a4 4 0 014 4c0 3-4 8-4 8S1 7 1 4a4 4 0 014-4z" fill="#666"/><circle cx="5" cy="4" r="1.5" fill="#fff"/></svg>Marlow Creek, PA &nbsp;|&nbsp; <svg width="11" height="11" viewBox="0 0 11 11" fill="none" stroke="#666"><circle cx="5.5" cy="5.5" r="4.5"/><path d="M5.5 3v3h2"/></svg>Full/Part-time</p>
    <a class="btn">Apply Now</a>
  </div>
  <div class="job" style="left:760px;top:388px">
    <svg width="60" height="60" viewBox="0 0 60 60" fill="none" stroke="#1565b8" stroke-width="2.5"><rect x="4" y="4" width="52" height="52" rx="6"/><path d="M4 16h52"/><path d="M22 26l-8 8 8 8M38 26l8 8-8 8M33 24l-6 20"/></svg>
    <h3>Program Manager</h3><p class="date">Posted on September 10, 2018</p>
    <p class="meta"><svg width="10" height="12" viewBox="0 0 10 12"><path d="M5 0a4 4 0 014 4c0 3-4 8-4 8S1 7 1 4a4 4 0 014-4z" fill="#666"/><circle cx="5" cy="4" r="1.5" fill="#fff"/></svg>Marlow Creek, PA &nbsp;|&nbsp; <svg width="11" height="11" viewBox="0 0 11 11" fill="none" stroke="#666"><circle cx="5.5" cy="5.5" r="4.5"/><path d="M5.5 3v3h2"/></svg>Full/Part-time</p>
    <a class="btn">Apply Now</a>
  </div>
</section>

<!-- Partners -->
<h2 class="section-title" style="top:3039px">OUR PARTNERS</h2>
<div class="abs partner-row">
  <svg class="abs" style="left:36px;top:20px" width="18" height="28" viewBox="0 0 18 28"><path d="M14 2L4 14l10 12" stroke="#aaa" stroke-width="2.5" fill="none"/></svg>
  <span class="partner" style="left:88px;width:76px;background:#1d4f9a"></span>
  <span class="partner" style="left:270px;width:92px;background:#4a7cc2"></span>
  <span class="partner" style="left:489px;width:37px;height:34px;top:9px;background:#d9302a"></span>
  <span class="partner" style="left:650px;width:102px;background:#3b3f7a"></span>
  <span class="partner" style="left:848px;width:88px;height:20px;top:16px;background:#1f6b35"></span>
  <span class="partner" style="left:1042px;width:86px;background:#c8102e"></span>
  <svg class="abs" style="left:1152px;top:20px" width="18" height="28" viewBox="0 0 18 28"><path d="M4 2l10 12L4 26" stroke="#aaa" stroke-width="2.5" fill="none"/></svg>
</div>

<!-- Contact -->
<div class="abs map" role="img" aria-label="Street map of the town around the office location"></div>
<section class="abs contact-panel">
  <h2>CONTACT</h2>
  <div class="c-item" style="top:143px">
    <span class="dot"><svg width="11" height="14" viewBox="0 0 10 12"><path d="M5 0a4 4 0 014 4c0 3-4 8-4 8S1 7 1 4a4 4 0 014-4z" fill="#fff"/><circle cx="5" cy="4" r="1.5" fill="#2a86e0"/></svg></span>
    <p class="lbl" style="font-size:18px;line-height:23px">4270 Alder Ridge Lane<br>Fenwick, OR 97021</p>
  </div>
  <div class="c-item" style="top:232px">
    <span class="dot"><svg width="14" height="14" viewBox="0 0 14 14"><path d="M3 1l3 3-2 2c1 2 2 3 4 4l2-2 3 3-2 2C6 13 1 8 1 3z" fill="#fff"/></svg></span>
    <div><p class="lbl">Telephone</p><p class="val">555.014.2290</p></div>
  </div>
  <div class="c-item" style="top:321px">
    <span class="dot"><svg width="14" height="11" viewBox="0 0 14 11"><rect x="0" y="0" width="14" height="11" rx="1" fill="#fff"/><path d="M1 1l6 5 6-5" stroke="#2a86e0" fill="none" stroke-width="1.5"/></svg></span>
    <div><p class="lbl">E mail</p><p class="val">info@velmatrix.com</p></div>
  </div>
</section>

<!-- Footer -->
<footer class="abs footer">
  <div class="flogo">VelmaTrix</div>
  <p class="fhead" style="left:474px">Contact Us</p>
  <div class="field" style="top:69px;height:31px">NAME</div>
  <div class="field" style="top:108px;height:31px">E MAIL</div>
  <div class="field" style="top:146px;height:60px">MESSAGE</div>
  <div class="submit">SUBMIT</div>
  <p class="fhead" style="left:774px">Menu</p>
  <ul class="fmenu"><li>HOME</li><li>SERVICES</li><li>PARTNER</li><li>CONTACT US</li><li>KARRIERE</li><li>ÜBER UNS</li><li>KONTAKT</li></ul>
  <p class="fhead" style="left:960px">Connect With Us</p>
  <div class="social" style="top:79px"><span class="c"></span>Friendwall</div>
  <div class="social" style="top:118px"><span class="c"></span>Chirpline</div>
  <div class="social" style="top:157px"><span class="c"></span>Workcircle</div>
  <span class="line"></span>
  <p class="copy">Copyrights @ 2019 All Rights Reserved</p>
</footer>

</body>
</html>
```